Hollowbrook Anglican Church Christmas Advertising

We need a postcard design for our upcoming Christmas events in Dec 2013

This is an exciting time of year and we want to give lots people in the local community a chance to celebrate Christmas with us

Key events
Songs by the Green Sat 14th Dec 5.00pm Corliss Park, Tamber St, Wrenford (opp church)
Christmas Eve Family Service 6.30pm
Christmas Eve Lessons and Carols 8.30pm
Christmas Day Celebration Service 9.30am

We have a church logo to include. Outline of the church with 2 lines, one green and one yellow line.
The advertising should be fun, punchy and bright colours. Possibly use a line such as Christmas Unwrapped...Jesus is the best present. (this is just an idea)

```html
<!DOCTYPE html>
<html lang="en">
<head>
<meta charset="utf-8">
<title>Hollowbrook Anglican Church – Christmas Postcard</title>
<link rel="stylesheet" href="https://fonts.googleapis.com/css2?family=Chewy&family=Open+Sans:wght@400;600;700&display=swap">
<style>
  :root {
    --page-bg: #ececec;
    --card-white: #ffffff;
    --front-light: #f4f4f4;
    --front-dark: #a9a9a9;
    --headline-red: #a3202a;
    --ink: #2a2a2a;
    --ink-soft: #3c3c3c;
    --footer-grey: #d9d9d9;
    --name-grey: #3a3a3a;
  }
  * { box-sizing: border-box; margin: 0; padding: 0; }
  html, body { width: 1200px; height: 900px; overflow: hidden; }
  body {
    background: var(--page-bg);
    font-family: "Open Sans", Arial, sans-serif;
    position: relative;
  }
  .postcard {
    position: absolute;
    top: 117px;
    width: 487px;
    height: 630px;
    box-shadow: 0 2px 6px rgba(0,0,0,0.18);
    overflow: hidden;
  }
  /* Front */
  .postcard--front {
    left: 73px;
    background: radial-gradient(ellipse at 50% 48%, var(--front-light) 0%, #d4d4d4 55%, var(--front-dark) 100%);
  }
  .advent-grid {
    position: absolute;
    top: 26px;
    left: 29px;
    display: grid;
    grid-template-columns: repeat(5, 73px);
    grid-auto-rows: 73px;
    column-gap: 16px;
    row-gap: 17px;
  }
  .advent-day {
    position: relative;
    border-radius: 50%;
    background: var(--c);
    display: flex;
    align-items: center;
    justify-content: center;
    font-family: "Chewy", "Comic Sans MS", cursive;
    font-size: 38px;
    color: #fff;
    line-height: 1;
    transform: none;
  }
  .advent-day::after {
    content: "";
    position: absolute;
    inset: 4px;
    border-radius: 50%;
    border: 1.5px dashed rgba(255,255,255,0.85);
  }
  .advent-day span { transform: rotate(-8deg); display: block; }
  .front-headline {
    position: absolute;
    top: 490px;
    left: 0;
    right: 0;
    text-align: center;
    font-family: "Chewy", "Comic Sans MS", cursive;
    font-size: 52px;
    line-height: 1.1;
    color: var(--headline-red);
    letter-spacing: 1px;
  }
  /* Back */
  .postcard--back {
    left: 633px;
    background: var(--card-white);
  }
  .church-name {
    position: absolute;
    top: 38px;
    left: 58px;
    display: flex;
    align-items: center;
    gap: 18px;
  }
  .church-name__mark {
    width: 22px;
    height: 22px;
    background: var(--headline-red);
  }
  .church-name__text {
    font-size: 34px;
    font-weight: 400;
    line-height: 1.15;
    color: var(--name-grey);
  }
  .invitation {
    position: absolute;
    top: 172px;
    left: 0;
    right: 0;
    text-align: center;
    color: var(--headline-red);
    font-weight: 700;
    font-size: 22px;
    line-height: 1.2;
  }
  .events {
    position: absolute;
    top: 298px;
    left: 0;
    right: 0;
    text-align: center;
    list-style: none;
    color: var(--ink);
  }
  .event { margin-bottom: 15px; }
  .event__title {
    font-size: 19px;
    font-weight: 600;
    line-height: 1.2;
  }
  .event__detail {
    font-size: 18px;
    line-height: 1.2;
    color: var(--ink-soft);
  }
  .event__detail--small { font-size: 14.5px; line-height: 1.35; }
  .contact-band {
    position: absolute;
    left: 0;
    right: 0;
    bottom: 0;
    height: 87px;
    background: var(--footer-grey);
    text-align: center;
    padding-top: 14px;
    font-size: 14.5px;
    line-height: 1.45;
    color: var(--ink);
  }
  .contact-band strong { font-weight: 600; }
</style>
</head>
<body>

<section class="postcard postcard--front" aria-label="Postcard front">
  <div class="advent-grid">
    <div class="advent-day" style="--c:#86b43a"><span>1</span></div>
    <div class="advent-day" style="--c:#9fcdec"><span>2</span></div>
    <div class="advent-day" style="--c:#d0262b"><span>3</span></div>
    <div class="advent-day" style="--c:#f2c21c"><span>4</span></div>
    <div class="advent-day" style="--c:#253a78"><span>5</span></div>

    <div class="advent-day" style="--c:#5b2a1a"><span>6</span></div>
    <div class="advent-day" style="--c:#6e2a72"><span>7</span></div>
    <div class="advent-day" style="--c:#c58fc4"><span>8</span></div>
    <div class="advent-day" style="--c:#26a2b1"><span>9</span></div>
    <div class="advent-day" style="--c:#f1b5c8"><span>10</span></div>

    <div class="advent-day" style="--c:#a11e2a"><span>11</span></div>
    <div class="advent-day" style="--c:#a6d8ea"><span>12</span></div>
    <div class="advent-day" style="--c:#5f8c35"><span>13</span></div>
    <div class="advent-day" style="--c:#f5e27a"><span>14</span></div>
    <div class="advent-day" style="--c:#d3821e"><span>15</span></div>

    <div class="advent-day" style="--c:#e0601e"><span>16</span></div>
    <div class="advent-day" style="--c:#1f3a7a"><span>17</span></div>
    <div class="advent-day" style="--c:#6b2a6e"><span>18</span></div>
    <div class="advent-day" style="--c:#b0205a"><span>19</span></div>
    <div class="advent-day" style="--c:#7fb53a"><span>20</span></div>

    <div class="advent-day" style="--c:#d25a9a"><span>21</span></div>
    <div class="advent-day" style="--c:#2a9a8a"><span>22</span></div>
    <div class="advent-day" style="--c:#9e1e24"><span>23</span></div>
    <div class="advent-day" style="--c:#c8282e"><span>24</span></div>
    <div class="advent-day" style="--c:#e3a21f" role="img" aria-label="Day 25 circle"></div>
  </div>
  <h1 class="front-headline">What's so special<br>about 25?</h1>
</section>

<section class="postcard postcard--back" aria-label="Postcard back">
  <div class="church-name">
    <div class="church-name__mark"></div>
    <div class="church-name__text">Hollowbrook<br>Anglican Church</div>
  </div>

  <h2 class="invitation">
    Jesus is the Reason for the<br>
    Christmas Season.<br>
    Come and celebrate with us at<br>
    Hollowbrook Anglican Church
  </h2>

  <ul class="events">
    <li class="event">
      <div class="event__title">Songs by the Green Sat</div>
      <div class="event__detail event__detail--small">14th Dec 5.00pm Corliss Park, Tamber St,<br>Wrenford (opp church)</div>
    </li>
    <li class="event">
      <div class="event__title">Christmas Eve</div>
      <div class="event__detail">Family Service 6.30pm</div>
    </li>
    <li class="event">
      <div class="event__title">Christmas Eve</div>
      <div class="event__detail">Lessons and Carols 8.30pm</div>
    </li>
    <li class="event">
      <div class="event__title">Christmas Day</div>
      <div class="event__detail">Celebration Service 9.30am</div>
    </li>
  </ul>

  <footer class="contact-band">
    <strong>Location:</strong><br>
    Cnr Ashgrove and Tamber St, Wrenford<br>
    Office: 02 5550 1234
  </footer>
</section>

</body>
</html>
```